Vernac Law Business cards and stationary design project

We are looking for a stationary design for business cards (double sided), 8x10, 5x7, and legal and standard envelopes.

We would like the design to match the logo that we have already.
Color palate preferred is Teal, White, grey and any others that will look good for a professional law firm.

We would like this statement: "RELATIONSHIPS. RESPECT. RESULT" to be on the back of the business cards and maybe on the stationary if it looks good.

Please see link to website for more information: www.vernac-law.example

Target Market(s)

Potential clients that need Attorney services.

Industry/Entity Type

Law Firm

Contact Information for Business Card

We would like the front and back to be two different colors. Current business cards are teal front, grey back and are a vertical design. We are open to options with colors.

Font styles to use
Serif

Colors
33a6d7
33b8a4
b9b9b9
5c5c5c

Requirements
Must have
• Logo supplied needs to go on the card and stationary.
• Match website color palate, www.vernac-law.example
• Be professional and not too wordy.
• Criminal Law, Civil Litigation, Personal Injury, Restraining Orders need to be on the card.
Nice to have
• RELATIONSHIPS. RESPECT. RESULTS. on the back of the card.
Should not have
• Not be too busy/wordy or too flashy.

```html
<!DOCTYPE html>
<html lang="en">
<head>
<meta charset="utf-8">
<title>Vernac Law Letterhead</title>
<link rel="stylesheet" href="https://fonts.googleapis.com/css2?family=Source+Sans+3:wght@400;600;700&display=swap">
<style>
  :root {
    --backdrop: #cfcfcf;
    --paper: #ececec;
    --teal: #1b7d8c;
    --teal-line: #2a97a6;
    --ink: #5a5a5a;
    --ink-dark: #1e1e1e;
    --band: #5c5c5c;
    --band-text: #f2f2f2;
    --sig-tone: #c4c4c4;
  }
  * { margin: 0; padding: 0; box-sizing: border-box; }
  html, body {
    width: 1200px; height: 1193px; overflow: hidden;
    background: var(--backdrop);
    font-family: "Source Sans 3", sans-serif;
  }
  .letterhead {
    position: absolute; left: 178px; top: 112px;
    width: 767px; height: 994px;
    background: var(--paper);
    color: var(--ink);
  }
  .brand {
    position: absolute; left: 68px; top: 100px;
    display: flex; align-items: center; gap: 14px;
  }
  .brand-square { width: 20px; height: 20px; background: var(--teal); }
  .brand-name {
    font-size: 34px; font-weight: 400; color: var(--teal);
    letter-spacing: 1px; line-height: 1;
  }
  .recipient {
    position: absolute; left: 68px; top: 294px;
    font-size: 13.5px;
  }
  .recipient .date { line-height: 20px; }
  .recipient .to { margin-top: 5px; line-height: 20px; }
  .recipient .org { line-height: 20px; font-size: 14.5px; }
  .salutation {
    position: absolute; left: 68px; top: 419px; font-size: 13.5px; line-height: 18px;
  }
  .body-copy {
    position: absolute; left: 68px; top: 455px; width: 636px;
    font-size: 13.8px; line-height: 18.2px;
  }
  .body-copy p { text-indent: 7px; margin-bottom: 18.2px; }
  .signature-mark {
    position: absolute; left: 68px; top: 784px;
    width: 132px; height: 50px; background: var(--sig-tone);
    border-radius: 4px;
  }
  .signer {
    position: absolute; left: 71px; top: 840px;
    font-size: 16px; line-height: 20px; font-weight: 700; color: var(--ink-dark);
  }
  .contact-band {
    position: absolute; left: 0; top: 926px; width: 767px; height: 38px;
    background: var(--band);
    border-top: 2px solid var(--teal-line);
    border-bottom: 2px solid var(--teal-line);
    display: flex; align-items: center; justify-content: center; gap: 11px;
    font-size: 12px; color: var(--band-text);
  }
  .contact-item { display: flex; align-items: center; gap: 4px; white-space: nowrap; }
  .contact-item svg { flex: none; }
  .motto {
    position: absolute; left: 0; top: 969px; width: 767px;
    text-align: center; font-size: 12.5px; line-height: 16px; color: var(--ink);
  }
</style>
</head>
<body>
  <main class="letterhead">
    <header class="brand">
      <span class="brand-square"></span>
      <span class="brand-name">Vernac Law</span>
    </header>

    <section class="recipient">
      <div class="date">December 24, 2015,</div>
      <div class="to">To: Reed Calloway</div>
      <div class="org">Northwind Holdings</div>
      <div class="org">City,State,Zip</div>
    </section>

    <div class="salutation">Dear Mr Calloway.</div>

    <section class="body-copy">
      <p>Lorem ipsum dolor sit amet, consectetur adipisicing elit, sed do eiusmod carte incididunt ut labore et dolore magna aliqua. Ut enim ad minim veniam, quis &nbsp;exercitation ullamco laboris nisi ut aliquip ex ea commodo consequat. review dolor in reprehenderit in voluptate .</p>
      <p>build voluptas sit aspernatur aut odit aut fugit, sed quia consequunture &nbsp;fugite ratione voluptatem equi nesciunt. Neque porro quisquam est, qui dolor ipsum sit amet, consectetur, adipisci velit, sed quia non numquam eius modilos iduim labore et dolore .</p>
      <p>Excepteur sint occaecat cupidatat non proident, sunt in culpa qui officia deser accusantium dolore mque laudantium, totam rem aperiam, eaque ipsa quae an ratione voluptatem sequi nesciunt. Nequ porro quisquam est, qui dolorem ie anim id est laborum. Sed ut perspiciatis unde omnis iste natus error sit volupte accusantium doloremque laudantium, totam rem aperiam, eaque ipsa quae ab verit atis et quasi architecto beatae vitae .</p>
      <p>Fuia voluptas sit aspernatur aut odit aut fugit, sed quia consequuntur magni &nbsp;ratione voluptatem sequi nesciunt. Neque porro quisquam est, qui dolorem eps sit amet, consectetur, adipisci velit, sed quia non numquam eius modi tempora &nbsp;labore et dolore .</p>
    </section>

    <div class="signature-mark" role="img" aria-label="Handwritten signature"></div>
    <div class="signer">Daniel Arden</div>

    <footer class="contact-band">
      <span class="contact-item">
        <svg width="9" height="12" viewBox="0 0 10 13"><path d="M5 0a5 5 0 0 0-5 5c0 3.5 5 8 5 8s5-4.5 5-8a5 5 0 0 0-5-5zm0 7a2 2 0 1 1 0-4 2 2 0 0 1 0 4z" fill="#2a97a6"/></svg>
        418 Harbor View Rd. #210 , Bayfield, CA 90000
      </span>
      <span class="contact-item">
        <svg width="11" height="11" viewBox="0 0 12 12"><path d="M2.5 0.5l2 2.5-1.2 1.3a7 7 0 0 0 4.4 4.4L9 7.5l2.5 2-1.3 1.8C5.5 11.5 0.5 6.5 0.7 1.8z" fill="#2a97a6"/></svg>
        (555) 014-2760
      </span>
      <span class="contact-item">
        <svg width="12" height="9" viewBox="0 0 13 10"><rect width="13" height="10" rx="1" fill="#2a97a6"/><path d="M0.5 1l6 4.5 6-4.5" fill="none" stroke="#5c5c5c" stroke-width="1"/></svg>
        mara@vernac-law.example
      </span>
      <span class="contact-item">
        <svg width="11" height="11" viewBox="0 0 12 12"><circle cx="6" cy="6" r="6" fill="#2a97a6"/><path d="M0 6h12M6 0c-3 3-3 9 0 12M6 0c3 3 3 9 0 12" fill="none" stroke="#5c5c5c" stroke-width="0.8"/></svg>
        www.vernac-law.example
      </span>
    </footer>

    <div class="motto">Counsel Clarity Commitment</div>
  </main>
</body>
</html>
```